Personal Web page for recruiter and owner of consulting firm

I work full time as a recruiter so I want a page that allows for me to support my efforts. I would like a long single page, I need to be able to upload four two minute videos, and 4 images. I also want the color scheme to match with my consulting company. I own the domain marcusfenwold.net already through wordpress . I took a shot at it myself and its terrible.

Target Market(s)

Potential clients

Industry/Entity Type

Management Consulting

Logo Text

marcus fenwold

Font styles to use
Serif

Requirements
Must have
• Must in color scheme go well with my consulting company logo attached
• Must be able to upload 4 two minute videos and 4 images (photos of me)
• Single long scroll page
• Modern and clean
Nice to have
• Easy for me to update videos images and text without complex coding
Should not have
• I want the design and feel to go well with my logos not exactly replicate it

```html
<!DOCTYPE html>
<html lang="en">
<head>
<meta charset="utf-8">
<title>Fenwold Strategies — Recruiting &amp; Consulting Firm</title>
<link href="https://fonts.googleapis.com/css2?family=Lora:ital,wght@0,400;0,500;0,700;1,400&family=Source+Serif+4:ital,wght@0,400;0,600;1,400&display=swap" rel="stylesheet">
<style>
  :root{
    --navy:#062d5e;
    --navy-deep:#0a2a55;
    --sky:#79b5e2;
    --sky-soft:#5fa2d8;
    --grey:#ebebeb;
    --ink:#222629;
    --muted:#5b6167;
    --white:#ffffff;
    --head:"Lora",Georgia,serif;
    --body:"Source Serif 4",Georgia,serif;
  }
  *{box-sizing:border-box;margin:0;padding:0}
  html,body{width:1200px;height:2965px;overflow:hidden}
  body{position:relative;background:var(--white);font-family:var(--body);color:var(--ink)}
  .abs{position:absolute}
  .heading{font-family:var(--head);font-weight:400;font-size:27px;letter-spacing:.5px;text-transform:uppercase;text-align:center;width:100%}

  /* hero */
  .hero{left:0;top:0;width:1200px;height:643px;background:linear-gradient(135deg,#b9a895 0%,#8d7b6a 40%,#6b6a6c 70%,#9a9389 100%)}
  .hero-shade{left:0;top:0;width:1200px;height:643px;background:rgba(20,25,35,.28)}
  .brand{left:134px;top:46px;font-family:var(--head);font-weight:400;color:var(--white);font-size:26px;line-height:1}
  .nav{right:138px;top:53px;display:flex;gap:30px;font-family:var(--head);font-size:15px;color:var(--white)}
  .hero-title{top:270px;font-family:var(--head);font-weight:700;font-size:44px;color:var(--white);text-align:center;width:100%}
  .hero-sub{top:338px;font-family:var(--head);font-weight:700;font-size:24px;letter-spacing:1px;color:var(--sky-soft);text-align:center;width:100%}
  .slider-dots{left:536px;top:600px;display:flex;gap:8px}
  .slider-dots span{width:28px;height:4px;background:var(--white)}
  .slider-dots span.on{background:var(--sky)}

  /* about */
  .about-photo{left:605px;top:643px;width:595px;height:450px;background:linear-gradient(120deg,#e9e6e2 0%,#c9c4bd 45%,#3b4555 75%,#2b3240 100%)}
  .about-title{left:142px;top:727px;font-family:var(--head);font-size:29px;font-weight:400}
  .about-copy{left:142px;top:780px;width:420px;font-size:13.5px;line-height:27px;color:var(--muted)}
  .about-copy p+p{margin-top:14px}
  .btn-outline{display:flex;align-items:center;justify-content:center;border:2px solid var(--navy);color:var(--navy);font-family:var(--head);font-size:12px;font-weight:500;letter-spacing:.5px}
  .about-btn{left:144px;top:945px;width:139px;height:38px}

  /* services */
  .services-band{left:0;top:1093px;width:1200px;height:490px}
  .services .heading{top:1128px;color:var(--white)}
  .service{width:300px;text-align:center;color:var(--white)}
  .service svg{display:block;margin:0 auto}
  .service h3{font-family:var(--head);font-weight:400;font-size:21px;margin-top:22px}
  .service p{font-size:12.5px;line-height:21px;margin:8px auto 0;width:290px;color:#d5deea}
  .service .btn-line{margin:22px auto 0;width:118px;height:34px;border:2px solid var(--white);display:flex;align-items:center;justify-content:center;font-family:var(--head);font-size:10.5px;font-weight:500}

  /* video */
  .video-band{left:0;top:1512px;width:1200px;height:514px;background:var(--grey)}
  .video .heading{top:1628px;color:#333}
  .video-frame{top:1746px;width:206px;height:140px;border:4px solid var(--white);box-shadow:0 2px 6px rgba(0,0,0,.25)}
  .video-frame .shot{width:100%;height:100%}
  .play{left:50%;top:50%;width:44px;height:44px;margin:-22px 0 0 -22px;border-radius:50%;background:var(--white);display:flex;align-items:center;justify-content:center}

  /* testimonials */
  .testi-band{left:0;top:2026px;width:1200px;height:386px;background:var(--sky)}
  .testi .heading{top:2074px;color:var(--white)}
  .avatar{width:100px;height:100px;border-radius:50%;border:4px solid var(--white);background:linear-gradient(160deg,#c9a98c,#7d6a5d)}
  .bubble{border:2px solid var(--white);border-radius:4px;padding:16px 20px;color:var(--white);font-style:italic;font-size:12.5px;line-height:21px}
  .author{color:var(--white);font-size:13px;line-height:17px}
  .author small{display:block;font-size:11px}

  /* contact */
  .contact-band{left:0;top:2412px;width:1200px;height:490px;background:linear-gradient(180deg,#f6f7f9,#eef0f3)}
  .contact .heading{top:2462px;color:#111}
  .info{left:198px;font-size:15.5px;color:#555;display:flex;align-items:flex-start;gap:14px;line-height:30px}
  .info svg{flex:none;margin-top:4px}
  .contact-brand{left:203px;top:2738px;font-family:var(--head);font-weight:400;color:var(--navy);font-size:26px;line-height:1}
  .socials{left:201px;top:2817px;display:flex;gap:9px}
  .socials span{width:29px;height:29px;background:var(--navy-deep)}
  .field{left:650px;width:400px;height:36px;background:var(--white);border:1px solid #d8dbe0;font-size:11.5px;color:#777;padding:9px 14px}
  .field.message{height:92px}
  .submit{left:650px;top:2803px;width:119px;height:38px;background:var(--sky);color:var(--white);font-family:var(--head);font-size:14px;display:flex;align-items:center;justify-content:center}

  /* footer */
  .footer{left:0;top:2902px;width:1200px;height:63px;background:var(--navy-deep);color:#c9d3e0;font-size:13px;display:flex;align-items:center;justify-content:center}
</style>
</head>
<body>

<header>
  <div class="abs hero" role="img" aria-label="Photo of a team meeting around an office table with laptops"></div>
  <div class="abs hero-shade"></div>
  <div class="abs brand">Fenwold Strategies</div>
  <nav class="abs nav">
    <span>About Us</span><span>Our Services</span><span>Videos</span><span>Testimonials</span><span>Contact</span>
  </nav>
  <h1 class="abs hero-title">RECRUITING &amp; CONSULTING FIRM</h1>
  <p class="abs hero-sub">SUSPENDISSE RISUS NIBH ULTRICIES VOLUTPAT</p>
  <div class="abs slider-dots"><span></span><span></span><span class="on"></span><span></span></div>
</header>

<section class="about">
  <h2 class="abs about-title">ABOUT COMPANY</h2>
  <div class="abs about-copy">
    <p>consectetuer augue nisi quis lacus Ut ac mi quis lacus mollis aliquam Curabitur iaculis tempus eros</p>
    <p>ultrices Ut nisi erat fermentum vel congue id euismod in elit Fusce ultricies orci ac feugiat suscipit leo massa sodales velit et scelerisque mi tortor at ipsum Proin orci odio</p>
  </div>
  <div class="abs btn-outline about-btn">READ MORE</div>
  <div class="abs about-photo" role="img" aria-label="Photo of two interviewers in suits facing a candidate across a desk"></div>
</section>

<section class="services">
  <svg class="abs services-band" width="1200" height="490" viewBox="0 0 1200 490">
    <polygon points="0,0 1200,0 1200,417 600,489 0,417" fill="var(--navy)"/>
  </svg>
  <h2 class="abs heading">OUR SERVICES</h2>

  <div class="abs service" style="left:148px;top:1222px">
    <svg width="80" height="80" viewBox="0 0 80 80" fill="none" stroke="#fff" stroke-width="3">
      <circle cx="37" cy="43" r="32"/><circle cx="37" cy="43" r="21"/><circle cx="37" cy="43" r="10"/>
      <line x1="37" y1="43" x2="72" y2="8"/><polyline points="62,6 72,8 74,18"/>
    </svg>
    <h3>Business Consulting</h3>
    <p>Pellentesque nibh libero ultricies eu sagittis non mollis sed justo Praesent metus ipsum pulvinar pulvinar porta fringilla</p>
    <div class="btn-line">READ MORE</div>
  </div>

  <div class="abs service" style="left:453px;top:1222px">
    <svg width="104" height="80" viewBox="0 0 104 80" fill="none" stroke="#fff" stroke-width="3" stroke-linejoin="round">
      <polyline points="2,24 20,24 20,50 2,50"/><polyline points="102,24 84,24 84,50 102,50"/>
      <path d="M20 28 L40 22 L56 30 L44 36 L36 32"/><path d="M84 28 L64 24 L50 26"/>
      <path d="M20 48 L34 60 L40 56 L46 62 L52 58 L58 62 L72 50 L84 48"/>
    </svg>
    <h3>Recruitment</h3>
    <p>Pellentesque nibh libero ultricies eu sagittis non mollis sed justo Praesent metus ipsum pulvinar pulvinar porta fringilla</p>
    <div class="btn-line" style="margin-top:16px">READ MORE</div>
  </div>

  <div class="abs service" style="left:781px;top:1222px">
    <svg width="80" height="80" viewBox="0 0 80 80" fill="#fff">
      <circle cx="32" cy="28" r="14"/>
      <path d="M6 74 Q8 48 32 46 Q56 48 58 74 Z"/>
      <rect x="46" y="6" width="28" height="18" rx="2" fill="none" stroke="#fff" stroke-width="3"/>
      <polygon points="52,24 50,32 58,24"/>
    </svg>
    <h3>Job Consulting</h3>
    <p>Pellentesque nibh libero ultricies eu sagittis non mollis sed justo Praesent metus ipsum pulvinar pulvinar porta fringilla</p>
    <div class="btn-line">READ MORE</div>
  </div>
</section>

<section class="video">
  <div class="abs video-band"></div>
  <svg class="abs" style="left:0;top:1509px" width="1200" height="76" viewBox="0 0 1200 76"><polygon points="0,0 1200,0 600,73" fill="var(--navy)"/></svg>
  <h2 class="abs heading">OUR VIDEO</h2>

  <div class="abs video-frame" style="left:160px">
    <div class="shot" role="img" aria-label="Video still of hands using a laptop and smartphone on a wooden table" style="background:linear-gradient(135deg,#3a3f46,#6b6f74 50%,#8a6a3c)"></div>
    <div class="abs play"><svg width="16" height="18" viewBox="0 0 16 18"><polygon points="2,0 16,9 2,18" fill="#111"/></svg></div>
  </div>
  <div class="abs video-frame" style="left:386px">
    <div class="shot" role="img" aria-label="Video still of a hand pointing at a tablet showing a recruitment screen" style="background:linear-gradient(135deg,#c9c6c1,#8f959b 50%,#cfcac3)"></div>
    <div class="abs play"><svg width="16" height="18" viewBox="0 0 16 18"><polygon points="2,0 16,9 2,18" fill="#111"/></svg></div>
  </div>
  <div class="abs video-frame" style="left:612px">
    <div class="shot" role="img" aria-label="Video still of a consultant speaking in a bright office" style="background:linear-gradient(135deg,#8d99a6,#5c6673 50%,#a8aeb5)"></div>
    <div class="abs play"><svg width="16" height="18" viewBox="0 0 16 18"><polygon points="2,0 16,9 2,18" fill="#111"/></svg></div>
  </div>
  <div class="abs video-frame" style="left:838px">
    <div class="shot" role="img" aria-label="Video still of a candidate interview across a meeting table" style="background:linear-gradient(135deg,#6f6458,#9b8f80 50%,#4a5260)"></div>
    <div class="abs play"><svg width="16" height="18" viewBox="0 0 16 18"><polygon points="2,0 16,9 2,18" fill="#111"/></svg></div>
  </div>
</section>

<section class="testi">
  <div class="abs testi-band"></div>
  <h2 class="abs heading">TESTIMONIALS</h2>

  <div class="abs avatar" style="left:156px;top:2145px" role="img" aria-label="Portrait of a client"></div>
  <div class="abs bubble" style="left:257px;top:2139px;width:296px;height:158px">Suspendisse risus nibh ultricies eu volutpat non condimentum hendrerit augue Etiam eleifend metus vitae adipiscing semper mauris ipsum iaculis elit con</div>
  <svg class="abs" style="left:245px;top:2184px" width="14" height="22" viewBox="0 0 14 22"><polyline points="13,0 1,11 13,22" fill="var(--sky)" stroke="#fff" stroke-width="2"/></svg>
  <p class="abs author" style="left:270px;top:2310px">By Author Name<small>City, Location</small></p>

  <div class="abs avatar" style="left:602px;top:2140px" role="img" aria-label="Portrait of a client"></div>
  <div class="abs bubble" style="left:712px;top:2135px;width:286px;height:154px">Etiam nulla massa pharetra facilisis volut pat in imperdiet sit amet sem Aliquam nec erat at purus cursus interd um Vestibulum ligula augue bibendum accumsan vesti</div>
  <svg class="abs" style="left:700px;top:2180px" width="14" height="22" viewBox="0 0 14 22"><polyline points="13,0 1,11 13,22" fill="var(--sky)" stroke="#fff" stroke-width="2"/></svg>
  <p class="abs author" style="left:716px;top:2305px">By Author Name<small>City, Location</small></p>
</section>

<section class="contact">
  <div class="abs contact-band" role="img" aria-label="Soft background photo of a white desk with keyboard and notebook"></div>
  <h2 class="abs heading">CONTACT US</h2>

  <div class="abs info" style="top:2556px">
    <svg width="26" height="26" viewBox="0 0 26 26"><rect width="26" height="26" fill="var(--navy-deep)"/><path d="M13 5a6 6 0 0 1 6 6c0 5-6 10-6 10s-6-5-6-10a6 6 0 0 1 6-6z" fill="#fff"/><circle cx="13" cy="11" r="2.2" fill="var(--navy-deep)"/></svg>
    <span>412 Alder Grove Road Suite B12<br>Marlow Falls, PA 19560</span>
  </div>
  <div class="abs info" style="top:2635px">
    <svg width="26" height="26" viewBox="0 0 26 26"><rect width="26" height="26" fill="var(--navy-deep)"/><path d="M8 6l3 0 1 4-2 1a9 9 0 0 0 5 5l1-2 4 1 0 3c-7 1-13-5-12-12z" fill="#fff"/></svg>
    <span>(555) 014-3872</span>
  </div>
  <div class="abs info" style="top:2670px">
    <svg width="26" height="22" viewBox="0 0 26 22"><rect width="26" height="22" fill="var(--navy-deep)"/><rect x="6" y="6" width="14" height="10" fill="#fff"/><polyline points="6,6 13,12 20,6" fill="none" stroke="var(--navy-deep)" stroke-width="1.5"/></svg>
    <span style="line-height:22px">info@companyname.com</span>
  </div>

  <div class="abs contact-brand">Fenwold Strategies</div>
  <div class="abs socials"><span></span><span></span><span></span><span></span><span></span></div>

  <div class="abs field" style="top:2555px">Name</div>
  <div class="abs field" style="top:2602px">Email address</div>
  <div class="abs field" style="top:2651px">Phone</div>
  <div class="abs field message" style="top:2700px">Message</div>
  <div class="abs submit">SUBMIT</div>
</section>

<footer class="abs footer">© 2017 Company Name&nbsp; All right reserved&nbsp; Term of Use</footer>

</body>
</html>
```